General contractor/GM consaltant business card

I need a card for my contracting company in North Dakota, we build industrial buildings for the oil feild and oil feild related companies offices, shops, airplain hangars, airports ext. We have a familly atmosphere on the job and are very relational and personal.
Industry/Entity Type
Industrial
Contact Information for Business Card
Ridgepost Contractors LLC.
Derek T.Holloway
4837 Tamarind dr. Colorado Springs, CO. 80917
Cell# 406-555-0148
derek@ridgepostcontractors.com

```html
<!DOCTYPE html>
<html lang="en">
<head>
<meta charset="utf-8">
<title>Ridgepost Contractors LLC. – Business Card</title>
<link rel="stylesheet" href="https://fonts.googleapis.com/css2?family=Arimo:wght@400;700&display=swap">
<style>
  :root {
    --bg: #e9e9ea;
    --card: #f7f7f7;
    --red: #d8262e;
    --red-dark: #b81d24;
    --blue: #2552a6;
    --shadow: rgba(0,0,0,0.18);
  }
  * { box-sizing: border-box; margin: 0; padding: 0; }
  html, body {
    width: 1200px; height: 858px; overflow: hidden;
    background: var(--bg);
    font-family: "Arimo", Arial, sans-serif;
  }
  .sheet {
    width: 1200px; height: 858px;
    display: flex; flex-direction: column;
    align-items: center; justify-content: center; gap: 64px;
  }
  .card {
    position: relative;
    width: 560px; height: 320px;
    background: var(--card);
    box-shadow: 0 10px 28px var(--shadow);
    overflow: hidden;
  }
  .card__band {
    position: absolute; left: 0; right: 0; height: 30px;
    background: linear-gradient(var(--red), var(--red-dark));
  }
  .card__band--top { top: 0; border-bottom: 5px solid var(--blue); height: 35px; }
  .card__band--bottom { bottom: 0; border-top: 5px solid var(--blue); height: 35px; }
  .card__body {
    position: absolute; top: 35px; bottom: 35px; left: 0; right: 0;
    display: flex; align-items: center; justify-content: center;
  }
  .brand {
    display: flex; align-items: center; gap: 10px;
    color: var(--red); font-weight: 700; letter-spacing: 0.2px;
  }
  .brand__mark { width: 14px; height: 14px; background: var(--blue); flex: none; }
  .front .card__body { flex-direction: column; gap: 0; }
  .front .brand { font-size: 26px; margin-bottom: 18px; }
  .contact__name { color: var(--red); font-size: 18px; margin-bottom: 14px; }
  .contact__line { color: var(--blue); font-size: 14px; line-height: 1.55; text-align: center; }
  .back .brand { font-size: 34px; gap: 14px; }
  .back .brand__mark { width: 18px; height: 18px; }
</style>
</head>
<body>
  <main class="sheet">
    <section class="card front" aria-label="Business card front">
      <div class="card__band card__band--top"></div>
      <div class="card__body">
        <div class="brand"><span class="brand__mark"></span>Ridgepost Contractors LLC.</div>
        <p class="contact__name">Derek T.Holloway</p>
        <p class="contact__line">406-555-0148</p>
        <p class="contact__line">4837 Tamarind dr. Colorado Springs, CO. 80917</p>
        <p class="contact__line">derek@ridgepostcontractors.com</p>
      </div>
      <div class="card__band card__band--bottom"></div>
    </section>

    <section class="card back" aria-label="Business card back">
      <div class="card__band card__band--top"></div>
      <div class="card__body">
        <div class="brand"><span class="brand__mark"></span>Ridgepost Contractors LLC.</div>
      </div>
      <div class="card__band card__band--bottom"></div>
    </section>
  </main>
</body>
</html>
```